FunBrixo Business Card

We need a business card design for our company. We sell construction-themed amusement rides for kids.

Contact Information for Business Card

Contact info on business card should include:
Carl Dunning
Co-Founder & COO
(833) 571-FUNBRIX
Carl@funbrixo-demo.com
www.funbrixo-demo.com

```html
<!DOCTYPE html>
<html lang="en">
<head>
<meta charset="UTF-8">
<title>FunBrixo Business Card</title>
<link rel="stylesheet" href="https://fonts.googleapis.com/css2?family=Arimo:wght@400;700&display=swap">
<style>
  :root {
    --bg: #3a3a3a;
    --card-gray: #8c8c8e;
    --card-black: #1b1b1b;
    --card-white: #ffffff;
    --orange: #f05a24;
    --hat-yellow: #f2b632;
    --pattern-blue: #2a6fc0;
    --text-light: #ffffff;
  }
  * { margin: 0; padding: 0; box-sizing: border-box; }
  html, body { width: 1200px; height: 1015px; overflow: hidden; }
  body {
    background: var(--bg);
    font-family: "Arimo", Arial, sans-serif;
    position: relative;
  }
  .card {
    position: absolute;
    width: 760px;
    height: 434px;
    overflow: hidden;
    box-shadow: 0 14px 30px rgba(0,0,0,0.45);
  }
  .brand-name {
    font-family: "Arimo", Arial, sans-serif;
    font-weight: 700;
    color: var(--orange);
    letter-spacing: 1px;
    white-space: nowrap;
  }

  /* Front */
  .card-front { left: 110px; top: 45px; background: var(--card-black); }
  .card-front .top-panel {
    position: absolute; left: 0; top: 0; width: 100%; height: 235px;
    background: var(--card-gray);
  }
  .card-front .crew-art {
    position: absolute; left: 60px; top: 24px; width: 640px; height: 290px;
    border-radius: 18px;
    background: linear-gradient(135deg, #f2b632 0%, #d98a3a 40%, #e7c9a8 70%, #9aa0a8 100%);
    opacity: 0.85;
  }
  .card-front .brand-name {
    position: absolute; left: 0; right: 0; top: 335px;
    text-align: center; font-size: 54px;
  }

  /* Back */
  .card-back { left: 330px; top: 530px; background: var(--card-white); }
  .card-back .info-band {
    position: absolute; left: 0; top: 150px; width: 100%; height: 190px;
    background: var(--card-black);
    border-top: 4px solid var(--orange);
    border-bottom: 4px solid var(--orange);
  }
  .card-back .duo-art {
    position: absolute; left: 45px; top: 40px; width: 220px; height: 190px;
    border-radius: 16px;
    background: linear-gradient(160deg, #f2b632 0%, #8a5a3c 45%, #3d6aa0 100%);
  }
  .card-back .brand-name {
    position: absolute; right: 50px; top: 52px; font-size: 52px;
  }
  .card-back .person {
    position: absolute; left: 45px; top: 258px;
  }
  .person-name {
    color: var(--orange); font-weight: 700; font-size: 27px; letter-spacing: 0.5px;
  }
  .person-title {
    color: var(--text-light); font-size: 21px; margin-top: 4px;
  }
  .contact-list {
    position: absolute; right: 60px; top: 178px; list-style: none;
  }
  .contact-list li {
    display: flex; align-items: center; gap: 12px;
    color: var(--text-light); font-size: 20px; margin-bottom: 11px;
    white-space: nowrap;
  }
  .contact-list svg { width: 22px; height: 22px; flex: none; }
  .card-back .pattern-strip {
    position: absolute; left: 0; bottom: 0; width: 100%; height: 90px;
    background: linear-gradient(180deg, #f5cf7a 0%, #8fb0d8 55%, #4a84c8 100%);
  }
</style>
</head>
<body>

<section class="card card-front">
  <div class="top-panel"></div>
  <div class="crew-art" role="img" aria-label="Cartoon construction crew in yellow hard hats"></div>
  <div class="brand-name">FunBrixo</div>
</section>

<section class="card card-back">
  <div class="info-band"></div>
  <div class="duo-art" role="img" aria-label="Two cartoon builders in hard hats and safety vests"></div>
  <div class="brand-name">FunBrixo</div>

  <div class="person">
    <div class="person-name">CARL DUNNING</div>
    <div class="person-title">Co-Founder &amp; COO</div>
  </div>

  <ul class="contact-list">
    <li>
      <svg viewBox="0 0 22 22" aria-hidden="true"><rect x="1" y="1" width="20" height="20" rx="3" fill="none" stroke="#f05a24" stroke-width="2"/><path d="M7 5l3 3-1.5 1.5a7 7 0 0 0 4 4L14 12l3 3-2 2c-5 0-10-5-10-10z" fill="#f05a24"/></svg>
      (833) 571-FUNBRIX
    </li>
    <li>
      <svg viewBox="0 0 22 22" aria-hidden="true"><rect x="1" y="4" width="20" height="14" fill="#f05a24"/><path d="M1 4l10 8 10-8" fill="none" stroke="#1b1b1b" stroke-width="1.6"/></svg>
      Carl@funbrixo-demo.com
    </li>
    <li>
      <svg viewBox="0 0 22 22" aria-hidden="true"><circle cx="11" cy="11" r="10" fill="#f05a24"/><g fill="none" stroke="#1b1b1b" stroke-width="1.3"><ellipse cx="11" cy="11" rx="4.5" ry="10"/><line x1="1" y1="11" x2="21" y2="11"/><line x1="3" y1="6" x2="19" y2="6"/><line x1="3" y1="16" x2="19" y2="16"/></g></svg>
      www.funbrixo-demo.com
    </li>
  </ul>

  <div class="pattern-strip" role="img" aria-label="Decorative band of repeated smiling hard-hat characters"></div>
</section>

</body>
</html>
```